Merry Meadow Roasters

We need a website to sell coffee with a horse theme. We already have a logo and have designed 4 different coffee bags/flavors so far, each of which will be available in ground or whole bean. The brand is intended to be light hearted/whimsical.

Requirements
Must have
• incorporation of attached photos
Nice to have
• underlying background theme with sky/grass

```html
<!DOCTYPE html>
<html lang="en">
<head>
<meta charset="utf-8">
<title>Merry Meadow Roasters</title>
<link href="https://fonts.googleapis.com/css2?family=Josefin+Sans:wght@600;700&family=Lato:wght@400;700&display=swap" rel="stylesheet">
<style>
:root{
  --espresso:#2c1b13;
  --roast:#3a2419;
  --tan:#c8955a;
  --tan-btn:#d9a66c;
  --sand:#e9c690;
  --cream:#ffffff;
  --ink:#1f1612;
  --muted:#6b5a4e;
  --line:#e6e1dc;
}
*{box-sizing:border-box;margin:0;padding:0}
html,body{width:1200px;height:4515px;overflow:hidden}
body{font-family:'Lato',sans-serif;color:var(--ink);background:#fff;position:relative}
.abs{position:absolute}
.head{font-family:'Josefin Sans',sans-serif;font-weight:700}
.btn{position:absolute;display:flex;align-items:center;justify-content:center;font-family:'Lato',sans-serif;font-weight:700;font-size:16px;letter-spacing:.3px;border-radius:3px;white-space:nowrap}
.btn-dark{background:var(--espresso);color:#fff}
.btn-tan{background:var(--tan-btn);color:var(--espresso)}
.ph{position:absolute}

/* hero */
.hero{position:absolute;left:0;top:0;width:1200px;height:641px;overflow:hidden}
.hero-photo{inset:0;background:radial-gradient(ellipse at 75% 40%,#c9a27a 0%,#7a4a2a 30%,#3a2114 65%,#1e120b 100%)}
.logo-disc{position:absolute;left:-40px;top:-120px;width:340px;height:300px;border-radius:50%;background:#fff}
.logo-name{position:absolute;left:40px;top:80px;width:190px;text-align:center;font-family:'Josefin Sans',sans-serif;font-weight:700;font-size:22px;line-height:1.15;color:var(--roast)}
.nav{position:absolute;top:43px;height:32px;display:flex;align-items:center;color:#fff;font-size:14px}
.nav a{position:absolute;color:#fff;text-decoration:none;white-space:nowrap}
.nav .active{background:var(--tan-btn);padding:8px 12px;border-radius:2px}
.hero h1{position:absolute;left:109px;top:200px;font-size:52px;line-height:68px;color:#fff;width:520px}
.hero .btn{left:110px;top:431px;width:249px;height:42px;background:#fff;color:var(--ink);font-size:15px}

/* products */
.section-title{position:absolute;font-family:'Josefin Sans',sans-serif;font-weight:700;font-size:46px;color:var(--ink);white-space:nowrap}
.section-title span{color:var(--tan)}
.bag{position:absolute;width:210px;height:300px;border-radius:6px;background:linear-gradient(180deg,#e3c194 0%,#caa171 70%,#3b2417 100%)}
.pname{position:absolute;font-size:20px;font-weight:700;letter-spacing:.3px;color:var(--ink);white-space:nowrap}
.card-hl{position:absolute;left:580px;top:834px;width:275px;height:476px;background:#fff;box-shadow:0 4px 18px rgba(0,0,0,.12)}
.price{position:absolute;font-family:'Josefin Sans',sans-serif;font-weight:700;font-size:30px;color:var(--tan)}

/* about */
.about-photo{left:0;top:1396px;width:597px;height:535px;background:linear-gradient(135deg,#3a2a20 0%,#6b4c36 45%,#c9b8a8 100%)}
.about-panel{position:absolute;left:597px;top:1396px;width:603px;height:535px;background:var(--sand)}
.body-text{font-size:15.5px;line-height:32.6px;color:var(--ink)}

/* offer */
.offer-art{left:44px;top:1980px;width:552px;height:455px;background:radial-gradient(ellipse at 55% 50%,#e8cca3 0%,#f6ecdf 55%,#fff 80%)}
.badge{position:absolute;left:400px;top:1992px;width:130px;height:130px;border-radius:50%;background:var(--tan);border:8px solid #f3e3cc;color:#fff;display:flex;align-items:center;justify-content:center;font-family:'Josefin Sans',sans-serif;font-weight:700;font-size:30px}
.offer-word{position:absolute;font-family:'Josefin Sans',sans-serif;font-weight:700;font-size:30px;color:var(--ink)}
.thumb{position:absolute;top:2239px;width:70px;height:100px;border-radius:4px;background:linear-gradient(180deg,#e3c194 0%,#c99f6e 70%,#3b2417 100%)}

/* testimonials */
.testi{position:absolute;left:0;top:2521px;width:1200px;height:470px;background:radial-gradient(ellipse at 50% 40%,#3d291d 0%,#2c1c14 70%)}
.tcard{position:absolute;left:0;top:0;width:1200px;height:470px;color:#fff}
.avatar{position:absolute;width:78px;height:78px;border-radius:50%;background:linear-gradient(135deg,#a87350,#5a3a26)}
.tname{position:absolute;font-weight:700;font-size:16px;white-space:nowrap}
.stars{position:absolute;color:#e2a63b;font-size:13px;letter-spacing:2px;white-space:nowrap}
.qmark{position:absolute;font-family:'Josefin Sans',sans-serif;font-size:44px;font-weight:700;color:#fff}
.thead{position:absolute;color:var(--tan);font-size:17px;font-weight:700;white-space:nowrap}
.ttext{position:absolute;font-size:13px;line-height:24px;color:#f1e8e0}
.arrow{position:absolute;width:26px;height:26px;border-radius:50%;display:flex;align-items:center;justify-content:center}

/* news */
.ncard{position:absolute;top:3171px;width:314px;height:375px;background:#fff;box-shadow:0 3px 14px rgba(0,0,0,.1)}
.nimg{position:absolute;left:0;top:0;width:314px;height:210px}
.ntag{position:absolute;left:14px;top:230px;color:var(--tan);font-size:15px}
.ntitle{position:absolute;left:14px;top:255px;width:290px;font-size:17px;line-height:26px;color:var(--ink)}
.nmeta{position:absolute;left:14px;top:323px;font-size:13px;color:var(--muted);display:flex;gap:30px;align-items:center;white-space:nowrap}
.nmeta span{display:flex;align-items:center;gap:6px}

/* subscribe */
.sub{position:absolute;left:110px;top:3635px;width:978px;height:395px;background:radial-gradient(ellipse at 78% 50%,#4a2d1c 0%,#24150e 55%,#15100c 100%)}
.field{position:absolute;background:#fff;border-radius:3px;font-size:14px;color:#555;padding-left:16px;display:flex;align-items:center}

/* footer */
.footer{position:absolute;left:0;top:4126px;width:1200px;height:389px;background:var(--espresso);color:#fff}
.fhead{position:absolute;top:110px;font-size:16px;font-weight:700;letter-spacing:.5px;white-space:nowrap}
.flinks{position:absolute;top:150px;font-size:13px;line-height:26.3px;white-space:nowrap}
.citem{position:absolute;display:flex;align-items:center;gap:20px;font-size:13px;white-space:nowrap}
.cicon{width:28px;height:28px;background:#fff;border-radius:4px;display:flex;align-items:center;justify-content:center}
</style>
</head>
<body>

<!-- HERO -->
<header class="hero">
  <div class="ph hero-photo" role="img" aria-label="Steaming cup of coffee on a saucer beside a coffee bag and scattered roasted beans on a wooden table"></div>
  <div class="logo-disc"></div>
  <div class="logo-name">Merry Meadow<br>Roasters</div>
  <nav class="nav" style="left:0;width:1200px">
    <a class="active" style="left:371px">Home</a>
    <a style="left:460px">About Us</a>
    <a style="left:548px">Products</a>
    <a style="left:645px">Testimonials</a>
    <a style="left:764px">Blog</a>
    <a style="left:832px">Contact Us</a>
  </nav>
  <svg class="abs" style="left:960px;top:38px" width="130" height="34" viewBox="0 0 130 34" fill="none" stroke="#fff" stroke-width="2.5">
    <circle cx="14" cy="14" r="10"/><line x1="21" y1="21" x2="29" y2="29"/>
    <circle cx="65" cy="11" r="7"/><path d="M52 31c0-8 6-12 13-12s13 4 13 12z"/>
    <path d="M100 6h5l4 19h16l3-13h-21"/><circle cx="111" cy="30" r="2"/><circle cx="122" cy="30" r="2"/>
  </svg>
  <h1 class="head">Galloping Into Your Mornings, One Cup at a Time!</h1>
  <div class="btn">Find Your Favorite Blend</div>
</header>

<!-- PRODUCTS -->
<section>
  <h2 class="section-title" style="left:459px;top:720px">Our <span>Products</span></h2>
  <div class="ph" style="left:757px;top:735px;width:112px;height:125px;border-radius:8px;background:linear-gradient(180deg,#f4e7d6,#d9c3a5)" role="img" aria-label="Illustrated horse jumping a fence with a rider"></div>

  <div class="bag" style="left:105px;top:855px" role="img" aria-label="Meadow Trot coffee bag with beans"></div>
  <div class="pname" style="left:106px;top:1178px">Meadow Trot</div>
  <div class="btn btn-tan" style="left:102px;top:1225px;width:137px;height:40px">SHOP NOW</div>

  <div class="bag" style="left:355px;top:855px" role="img" aria-label="Sunny Canter coffee bag with beans"></div>
  <div class="pname" style="left:354px;top:1178px">Sunny Canter</div>
  <div class="btn btn-tan" style="left:351px;top:1225px;width:137px;height:40px">SHOP NOW</div>

  <div class="card-hl"></div>
  <div class="bag" style="left:630px;top:875px;width:175px;height:265px" role="img" aria-label="Hilltop Blend coffee bag with beans"></div>
  <svg class="abs" style="left:806px;top:872px" width="30" height="100" viewBox="0 0 30 100">
    <circle cx="15" cy="14" r="12" fill="#e5374a"/><path d="M15 20l-6-6a3.5 3.5 0 0 1 6-4 3.5 3.5 0 0 1 6 4z" fill="#fff"/>
    <path d="M5 42h4l3 12h12l3-9H11" fill="none" stroke="#2c1b13" stroke-width="2"/><circle cx="13" cy="58" r="1.6" fill="#2c1b13"/><circle cx="22" cy="58" r="1.6" fill="#2c1b13"/>
    <g stroke="#2c1b13" stroke-width="2"><line x1="4" y1="80" x2="26" y2="80"/><line x1="4" y1="87" x2="26" y2="87"/><line x1="4" y1="94" x2="26" y2="94"/></g>
    <g fill="#fff" stroke="#2c1b13" stroke-width="1.6"><circle cx="18" cy="80" r="2.5"/><circle cx="10" cy="87" r="2.5"/><circle cx="20" cy="94" r="2.5"/></g>
  </svg>
  <div class="pname" style="left:580px;width:275px;text-align:center;top:1158px">Hilltop Blend</div>
  <div class="price" style="left:580px;width:275px;text-align:center;top:1192px">$43.00</div>
  <div class="btn btn-dark" style="left:648px;top:1240px;width:139px;height:42px">ADD TO CART</div>

  <div class="bag" style="left:875px;top:855px" role="img" aria-label="Clover Dash coffee bag with beans"></div>
  <div class="pname" style="left:876px;top:1178px">Clover Dash</div>
  <div class="btn btn-tan" style="left:872px;top:1225px;width:139px;height:40px">SHOP NOW</div>
</section>

<!-- ABOUT -->
<section>
  <div class="ph about-photo" role="img" aria-label="Woman in a cafe looking at her phone beside a cup of coffee"></div>
  <div class="about-panel">
    <h2 class="head" style="position:absolute;left:48px;top:70px;font-size:46px">About Us</h2>
    <p class="body-text" style="position:absolute;left:48px;top:132px;width:455px">At Merry Meadow Roasters, we believe that coffee should be as adventurous and spirited as a wild stallion—bold, energetic, and always a little bit unexpected! Our journey began when we realized there was a gap in the world of coffee: where was the fun, the whimsy, the joy? We wanted to bring something more to the table (or should we say, the stable?), so we set out to create a coffee experience that could make your mornings feel like a gallop through the open fields.</p>
    <div class="btn btn-dark" style="left:46px;top:419px;width:138px;height:42px">READ MORE</div>
  </div>
</section>

<!-- SPECIAL OFFER -->
<section>
  <div class="ph offer-art" role="img" aria-label="Cartoon rider on a grey horse beside a Sunny Canter coffee bag surrounded by beans"></div>
  <div class="badge">20%</div>
  <div class="offer-word" style="left:112px;top:2207px">SUNNY</div>
  <div class="offer-word" style="left:462px;top:2207px">CANTER</div>
  <h2 class="head" style="position:absolute;left:645px;top:2010px;font-size:44px;line-height:58px;width:420px">Special offer <span style="color:var(--tan)">Get Your Discount</span></h2>
  <p style="position:absolute;left:645px;top:2135px;width:440px;font-size:13.5px;line-height:31px;color:var(--muted)">Our beans are hand-picked and roasted to perfection, ensuring that each cup of Merry Meadow Roasters coffee is nothing short of extraordinary.</p>
  <div class="thumb" style="left:645px" role="img" aria-label="Meadow Trot bag"></div>
  <div class="thumb" style="left:750px" role="img" aria-label="Sunny Canter bag"></div>
  <div class="thumb" style="left:855px" role="img" aria-label="Hilltop Blend bag"></div>
  <div class="thumb" style="left:960px" role="img" aria-label="Clover Dash bag"></div>
  <div class="btn btn-dark" style="left:645px;top:2386px;width:138px;height:44px">BUY NOW</div>
</section>

<!-- TESTIMONIALS -->
<section class="testi">
  <h2 class="head" style="position:absolute;left:0;width:1200px;text-align:center;top:68px;font-size:44px;color:#fff">Client Testimonials</h2>
  <div class="arrow" style="left:36px;top:269px;background:#fff">
    <svg width="14" height="14" viewBox="0 0 14 14"><path d="M12 7H3M7 2L2 7l5 5" fill="none" stroke="#2c1b13" stroke-width="2.2"/></svg>
  </div>
  <div class="arrow" style="left:1126px;top:269px;border:2px solid #6b5446">
    <svg width="14" height="14" viewBox="0 0 14 14"><path d="M2 7h9M7 2l5 5-5 5" fill="none" stroke="#6b5446" stroke-width="2.2"/></svg>
  </div>
  <div class="abs" style="left:598px;top:185px;height:210px;border-left:2px dashed var(--tan)"></div>

  <div class="tcard">
    <div class="avatar" style="left:118px;top:155px" role="img" aria-label="Customer portrait"></div>
    <div class="tname" style="left:221px;top:170px">Lena P.</div>
    <div class="stars" style="left:221px;top:203px">★★★★★</div>
    <div class="qmark" style="left:510px;top:162px">”</div>
    <div class="thead" style="left:114px;top:261px">Galloping into my mornings has never been easier!</div>
    <p class="ttext" style="left:114px;top:291px;width:440px">"I never thought I'd find a coffee that makes me giddy with excitement, but here we are! The flavors are incredible, and the whole horse theme just adds the perfect touch of fun. I've never been so eager to trot to my coffee pot!"</p>
  </div>
  <div class="tcard">
    <div class="avatar" style="left:650px;top:155px" role="img" aria-label="Customer portrait"></div>
    <div class="tname" style="left:752px;top:170px">Mara K.</div>
    <div class="stars" style="left:752px;top:203px">★★★★★</div>
    <div class="qmark" style="left:1042px;top:162px">”</div>
    <div class="thead" style="left:646px;top:261px">Coffee that keeps me stirrup-ed!</div>
    <p class="ttext" style="left:646px;top:291px;width:440px">"If you're looking for a coffee that's as smooth as a canter and as bold as a gallop, look no further! The quality is unmatched, and I can't get enough of the fun packaging. I feel like I'm riding into a coffee paradise with every cup!"</p>
  </div>
</section>

<!-- NEWS -->
<section>
  <h2 class="section-title" style="left:116px;top:3075px;font-size:44px">Latest <span>News</span></h2>
  <div class="btn btn-dark" style="left:950px;top:3080px;width:136px;height:42px">VIEW ALL</div>

  <article class="ncard" style="left:110px">
    <div class="ph nimg" style="background:linear-gradient(135deg,#5a3d2b,#a97b58 60%,#d8bfa3)" role="img" aria-label="Woman smiling while holding a coffee cup"></div>
    <div class="ntag">News</div>
    <div class="ntitle">A Horse Lover's Guide to Perfect Pairings</div>
    <div class="nmeta"><span>▦ Feb 17,2025</span><span>▭ 4 Comments</span></div>
  </article>
  <article class="ncard" style="left:441px">
    <div class="ph nimg" style="background:linear-gradient(135deg,#e9e6df,#b9aa98 55%,#4a5a3a)" role="img" aria-label="Woman at a desk sipping coffee by a window"></div>
    <div class="ntag">News</div>
    <div class="ntitle">The Secret Lives of Horses and How They Inspired Our Coffee</div>
    <div class="nmeta"><span>▦ Feb 19,2025</span><span>▭ 4 Comments</span></div>
  </article>
  <article class="ncard" style="left:771px">
    <div class="ph nimg" style="background:linear-gradient(135deg,#4a3022,#8a5a3c 55%,#c9a785)" role="img" aria-label="Barista pouring coffee at an espresso machine"></div>
    <div class="ntag">News</div>
    <div class="ntitle">Brewing with Horsepower: Best Methods for Your Coffee</div>
    <div class="nmeta"><span>▦ Feb 21,2025</span><span>▭ 4 Comments</span></div>
  </article>
</section>

<!-- SUBSCRIBE -->
<section class="sub" role="img" aria-label="Dark backdrop of roasted coffee beans with a coffee bag">
  <h2 class="head" style="position:absolute;left:48px;top:50px;font-size:44px;line-height:60px;color:#fff">Subscribe To Our<br>Newsletter</h2>
  <div class="field" style="left:48px;top:174px;width:196px;height:42px">Name</div>
  <div class="field" style="left:254px;top:174px;width:197px;height:42px">Phone</div>
  <div class="field" style="left:48px;top:226px;width:403px;height:44px">Email Address</div>
  <div class="btn btn-tan" style="left:50px;top:286px;width:139px;height:42px;color:#fff">SUBSCRIBE</div>
  <div class="ph" style="left:717px;top:100px;width:130px;height:200px;border-radius:6px;background:linear-gradient(180deg,#e3c194,#c99f6e 70%,#3b2417)"></div>
</section>

<!-- FOOTER -->
<footer class="footer">
  <div class="abs head" style="left:150px;top:135px;width:230px;text-align:center;font-size:30px;line-height:1.2;font-weight:600">Merry Meadow<br>Roasters</div>

  <div class="fhead" style="left:482px">Quick Links</div>
  <div class="flinks" style="left:486px">Home<br>About Us<br>Products<br>Testimonials<br>Blog<br>Contact Us</div>

  <div class="fhead" style="left:662px">Other Links</div>
  <div class="flinks" style="left:663px">Privacy Policy<br>Terms Of Conditions<br>Disclaimer<br>FAQ's<br>Support<br>Help</div>

  <div class="fhead" style="left:867px">Contact Info</div>
  <div class="citem" style="left:870px;top:149px"><span class="cicon"><svg width="14" height="18" viewBox="0 0 14 18"><path d="M7 1a6 6 0 0 1 6 6c0 4-6 10-6 10S1 11 1 7a6 6 0 0 1 6-6z" fill="#2c1b13"/><circle cx="7" cy="7" r="2.2" fill="#fff"/></svg></span>12 Meadow Lane, USA - 40100</div>
  <div class="citem" style="left:870px;top:198px"><span class="cicon"><svg width="16" height="16" viewBox="0 0 16 16"><path d="M3 1l3 1 1 4-2 1a9 9 0 0 0 4 4l1-2 4 1 1 3-2 2C7 15 1 9 1 3z" fill="#2c1b13"/></svg></span>+1 555 010 2040</div>
  <div class="citem" style="left:870px;top:249px"><span class="cicon"><svg width="16" height="12" viewBox="0 0 16 12"><rect x="1" y="1" width="14" height="10" fill="#2c1b13"/><path d="M1 1l7 6 7-6" fill="none" stroke="#fff" stroke-width="1.4"/></svg></span>hello@merrymeadow.example</div>

  <div class="abs" style="left:110px;top:331px;width:978px;border-top:1px solid #6b5446"></div>
  <div class="abs" style="left:0;width:1200px;top:349px;text-align:center;font-size:13px">© 2025 Merry Meadow Roasters. All rights reserved.</div>
</footer>

</body>
</html>
```